Updated website design needed for Radiology Group, Pine Hollow Imaging Partners

Clean, uncluttered, updated design needed for top regional Radiology Center. Focus on personal, patient oriented design, (not clinical). Should be simple and easy to navigate, with clear CTAs. Use blues, greens and photos of people in the Central Oregon outdoors.
Uncoded, PSD design only. 2 pages: Home page and one example interior page.
reference current site: http://www.phipclinic-example.com/
Sites they like:
http://www.valescanlabs-example.com/
http://www.tbmx-example.net/handler.cfm?event=practice,main
http://www.kestrelbonecare-example.com/

Medical Imaging

2 page

Sans Serif

• Personal and patient friendly.
• Lots of white space, clean and uncluttered. Clear CTAs, such as: Patient Bill Pay, Make an Appointment, Meet Our Doctors
• Use copy and contact information from the current site.
• Use outdoor images from Central Oregon, late Winter/ Spring (snow, light colors, spring green, for example)
• Include one example interior page, either Your Exam or Meet Our Doctors
• The client likes:
• Meet Our Doctors slider section, and big, easy to navigate Information Center on www.kestrelbonecare-example.com
• The personal feel of the Your Exam section on www.valescanlabs-example.com
• Blues and Greens, outdoorsy imagery
• The client does not like:
• complex drop down menus
• clinical feel
• Do not use lorum ipsum or dummy text.
• Do not use outdoor images from other regions. Do not use Summer (hot, poolside) or Fall (red/orange leaves) images.

```html
<!DOCTYPE html>
<html lang="en">
<head>
<meta charset="utf-8">
<title>Pine Hollow Imaging Partners</title>
<link href="https://fonts.googleapis.com/css2?family=Open+Sans:wght@400;600;700&family=Rajdhani:wght@500;600;700&family=Russo+One&display=swap" rel="stylesheet">
<style>
:root{
  --cyan:#00b7f1;
  --green:#8bbd0d;
  --ink:#2f2f2f;
  --text:#444;
  --light:#e9ecf3;
  --grey:#f0f0f0;
  --dark:#333333;
  --darker:#242424;
  --white:#ffffff;
}
*{box-sizing:border-box;margin:0;padding:0}
html,body{width:1200px;height:2616px;overflow:hidden;background:var(--white)}
body{position:relative;font-family:"Open Sans",sans-serif;color:var(--text)}
a{text-decoration:none}
.abs{position:absolute}
.heading{font-family:"Rajdhani",sans-serif;font-weight:500;color:var(--ink);text-align:center}

/* header */
.site-header{left:0;top:0;width:1200px;height:96px;background:#fafafa;border-top:3px solid var(--cyan)}
.brand{left:162px;top:18px;display:flex;align-items:center;gap:12px}
.brand-mark{width:58px;height:58px;background:#7478ae}
.brand-name{font-weight:600;font-size:17px;line-height:21px;color:#2b3170;width:150px}
.top-cta{left:706px;top:0;height:30px;display:flex}
.top-phone{background:var(--cyan);color:#fff;font-weight:700;font-size:16px;padding:0 16px 0 14px;display:flex;align-items:center;gap:10px;border-radius:0 0 0 14px}
.top-book{background:var(--green);color:#fff;font-weight:600;font-size:14px;padding:0 22px 0 14px;display:flex;align-items:center;clip-path:polygon(0 0,100% 0,92% 100%,0 100%)}

.main-nav{left:0;top:96px;width:1200px;height:40px;background:var(--cyan);display:flex;align-items:center;padding-left:143px}
.main-nav a{color:#fff;font-size:12px;height:40px;line-height:40px;padding:0 17px}
.main-nav a.active{background:var(--green);font-weight:700}

/* hero */
.hero{left:0;top:136px;width:1200px;height:411px;background:linear-gradient(180deg,#9aa7b8 0%,#b9b3bd 14%,#8d8790 26%,#3f5a3a 40%,#2c4228 52%,#5f7480 62%,#8d9aa0 70%,#3e5030 82%,#7a8a4c 100%)}
.hero-caption{left:0;top:460px;width:1200px;height:87px;background:rgba(30,30,30,.55)}
.hero-caption p{font-family:"Rajdhani",sans-serif;font-weight:500;color:#fff;font-size:28px;line-height:37px;text-align:center;padding-top:7px}

/* welcome */
.welcome-title{left:0;top:590px;width:1200px;font-size:31px}
.welcome-text{left:166px;top:680px;width:868px;font-size:12.5px;line-height:23px;text-align:center;color:#333}
.btn{display:inline-block;background:var(--cyan);color:#fff;font-weight:700;font-size:12px;text-align:center}
.welcome-btn{left:550px;top:792px;width:98px;height:33px;line-height:33px}

/* services */
.services{left:0;top:877px;width:1200px;height:549px;background:var(--light)}
.services-title{left:0;top:905px;width:1200px;font-size:31px}
.service-card{width:284px;height:185px;background:#fff;padding:6px 6px 0;box-shadow:0 1px 3px rgba(0,0,0,.08)}
.service-card .shot{width:272px;height:119px}
.service-card .label{position:absolute;left:0;bottom:0;width:284px;height:59px;background:var(--cyan);color:#fff;font-family:"Rajdhani",sans-serif;font-weight:500;font-size:22px;line-height:59px;text-align:center}
.service-card .label.lead{background:var(--green)}

/* audience split */
.audience{top:1426px;width:600px;height:338px;text-align:center;color:#fff}
.audience.patients{left:0;background:linear-gradient(120deg,#4e4a45,#7a7068 45%,#9a8f86 60%,#5a544f)}
.audience.physicians{left:600px;background:linear-gradient(120deg,#1cb8ee,#5ccdf4 45%,#8fd9f5 60%,#17aee4)}
.audience h2{font-family:"Russo One",sans-serif;font-weight:400;font-size:29px;margin-top:12px}
.audience p{font-size:14px;line-height:25px;width:430px;margin:6px auto 0}
.audience .btn-white{display:inline-block;margin-top:18px;background:#fff;color:#333;font-weight:600;font-size:12px;width:98px;height:33px;line-height:33px}
.audience svg{margin-top:30px}

/* bill pay + physicians */
.block-title{font-family:"Rajdhani",sans-serif;font-weight:500;font-size:28px;color:var(--ink);border-bottom:1px solid #ddd;padding-bottom:8px}
.billpay{left:161px;top:1808px;width:404px}
.billpay-shot{left:161px;top:1864px;width:196px;height:128px;background:linear-gradient(135deg,#eef2f5,#b9c9d8 40%,#3a6fa8 55%,#c9d4de 70%,#f2f4f6)}
.billpay-links{left:372px;top:1866px;width:200px;list-style:none}
.billpay-links li{font-size:11px;font-weight:700;line-height:18px;margin-bottom:16px;display:flex;gap:6px}
.billpay-links li a{color:#333;text-decoration:underline}
.billpay-links li span{color:var(--cyan)}
.doctors{left:628px;top:1808px;width:410px}
.doctor{top:1866px;width:94px;height:119px}
.doctor .shot{width:94px;height:119px}
.doctor .name{position:absolute;left:0;bottom:0;width:94px;height:21px;background:var(--cyan);color:#fff;font-size:10px;line-height:21px;text-align:center}

/* reviews */
.reviews{left:0;top:2044px;width:1200px;height:330px;background:var(--grey)}
.reviews-title{left:0;top:2068px;width:1200px;font-size:28px}
.review-avatar{left:170px;top:2134px;width:110px;height:110px;border-radius:50%;border:4px solid #333;background:linear-gradient(180deg,#e4e8ea,#b9a596 55%,#8a96a4)}
.review-text{left:318px;top:2142px;width:712px;font-size:11.5px;line-height:21px;color:#333}
.review-rule{left:318px;top:2244px;width:712px;height:1px;background:#ccc}
.review-name{left:318px;top:2249px;font-size:15px;font-weight:700;font-style:italic;color:var(--cyan)}

/* footer */
.footer-shape{left:0;top:2300px}
.footer-col{top:2392px;color:#ddd}
.footer-col h3{font-size:14px;font-weight:700;color:#fff;border-bottom:1px solid #555;padding-bottom:8px;margin-bottom:10px}
.links{display:grid;grid-template-columns:110px 110px;row-gap:6px;list-style:none}
.links li{font-size:10.5px;color:#ddd}
.links li::before{content:"› ";color:#aaa}
.inquiry input,.inquiry textarea{display:block;width:190px;background:#fff;border:none;font-size:9px;padding:3px 6px;margin-bottom:5px;font-family:"Open Sans",sans-serif;color:#999}
.inquiry input{height:18px}
.inquiry textarea{height:34px;resize:none}
.inquiry button{background:var(--green);color:#fff;border:none;font-size:10px;padding:3px 8px;font-family:"Open Sans",sans-serif}
.contact li{list-style:none;font-size:10.5px;line-height:16px;display:flex;gap:12px;margin-bottom:18px}
.vrule{top:2392px;width:1px;height:136px;background:#555}
.bottom-bar{left:0;top:2578px;width:1200px;height:38px;background:var(--darker)}
.bottom-bar p{position:absolute;left:162px;top:11px;font-size:10.5px;color:#ccc}
.social{position:absolute;top:8px;width:24px;height:24px;border-radius:50%}
</style>
</head>
<body>

<header class="abs site-header">
  <div class="abs brand"><span class="brand-mark"></span><span class="brand-name">Pine Hollow Imaging Partners</span></div>
  <div class="abs top-cta">
    <div class="top-phone">
      <svg width="14" height="14" viewBox="0 0 24 24"><path fill="#fff" d="M6.6 10.8a15 15 0 0 0 6.6 6.6l2.2-2.2c.3-.3.7-.4 1-.2 1.1.4 2.3.6 3.6.6.6 0 1 .4 1 1V20c0 .6-.4 1-1 1A17 17 0 0 1 3 4c0-.6.4-1 1-1h3.5c.6 0 1 .4 1 1 0 1.3.2 2.5.6 3.6.1.3 0 .7-.2 1z"/></svg>
      555 010 4821
    </div>
    <div class="top-book">Book An Appointment</div>
  </div>
</header>

<nav class="abs main-nav">
  <a class="active" href="#">Home</a><a href="#">About Us</a><a href="#">Our Services</a><a href="#">For Patients</a><a href="#">Our Physicians</a><a href="#">For Physicians</a><a href="#">PACS &amp; Documents</a><a href="#">Appointments</a><a href="#">Our Locations</a>
</nav>

<section class="abs hero" role="img" aria-label="Hiker with a backpack beside a still mountain lake, a snow-streaked peak and pine forest reflected in the water"></section>
<div class="abs hero-caption"><p>Provide Quality Diagnostic Imaging Services To The<br>Central And Eastern Oregon Communities</p></div>

<h1 class="abs heading welcome-title">Welcome to Pine Hollow Imaging Partners</h1>
<svg class="abs" style="left:0;top:636px" width="1200" height="30"><line x1="386" y1="15" x2="584" y2="15" stroke="#ccc"/><line x1="616" y1="15" x2="814" y2="15" stroke="#ccc"/><circle cx="600" cy="15" r="9" fill="#8f9fc7"/></svg>
<p class="abs welcome-text">For decades our radiologists have served patients across Central and Eastern Oregon with careful, unhurried care. We offer MRI, CT, X-ray, nuclear medicine, PET and ultrasound close to home, with friendly technologists who take time to explain each step of your exam. Our board-certified physicians read every study promptly and share clear results with your doctor, so you can get back to the trails, the rivers and the people you love sooner. We are glad you are here.</p>
<a class="abs btn welcome-btn" href="#">Read More</a>

<section class="abs services"></section>
<h2 class="abs heading services-title">Our Services</h2>
<svg class="abs" style="left:0;top:946px" width="1200" height="30"><line x1="386" y1="15" x2="584" y2="15" stroke="#c8ccd6"/><line x1="616" y1="15" x2="814" y2="15" stroke="#c8ccd6"/><circle cx="600" cy="15" r="9" fill="#8f9fc7"/></svg>

<div class="abs service-card" style="left:161px;top:995px"><div class="shot" role="img" aria-label="MRI scanner in a bright room" style="background:linear-gradient(90deg,#c9ced3,#f4f5f6 35%,#dfe2e5 70%,#eef0f2)"></div><div class="label lead">MRI</div></div>
<div class="abs service-card" style="left:459px;top:995px"><div class="shot" role="img" aria-label="CT scanner with patient table" style="background:linear-gradient(90deg,#f6f7f8,#d9dde0 45%,#b7bdc2 60%,#f4f5f6)"></div><div class="label">CT-64</div></div>
<div class="abs service-card" style="left:756px;top:995px"><div class="shot" role="img" aria-label="X-ray of two hands" style="background:linear-gradient(90deg,#0e0e0e,#7a7a7a 25%,#1b1b1b 45%,#8a8a8a 70%,#111)"></div><div class="label">X-Ray</div></div>
<div class="abs service-card" style="left:161px;top:1205px"><div class="shot" role="img" aria-label="Nuclear medicine scanner" style="background:linear-gradient(90deg,#dfe5e8,#9fb3b8 45%,#6f8c90 55%,#e6ebee)"></div><div class="label">Nuclear Medicine</div></div>
<div class="abs service-card" style="left:459px;top:1205px"><div class="shot" role="img" aria-label="PET scanner room with green wall" style="background:linear-gradient(90deg,#f2f3f1,#e0e3e2 45%,#cfd8cc 70%,#5f9a5c)"></div><div class="label">PET</div></div>
<div class="abs service-card" style="left:756px;top:1205px"><div class="shot" role="img" aria-label="Ultrasound scan image" style="background:radial-gradient(ellipse at 45% 55%,#6e6e6e,#2a2a2a 45%,#0c0c0c 75%)"></div><div class="label">Ultrasound</div></div>

<section class="abs audience patients" role="img" aria-label="Doctor consulting with a patient">
  <svg width="80" height="76" viewBox="0 0 80 76"><circle cx="16" cy="10" r="8" fill="#fff"/><rect x="8" y="21" width="16" height="32" rx="3" fill="#fff"/><rect x="10" y="52" width="5" height="22" fill="#fff"/><rect x="17" y="52" width="5" height="22" fill="#fff"/><rect x="30" y="8" width="46" height="38" fill="none" stroke="#fff" stroke-width="4"/><line x1="22" y1="30" x2="40" y2="22" stroke="#fff" stroke-width="4"/><line x1="53" y1="46" x2="44" y2="62" stroke="#fff" stroke-width="3"/><line x1="53" y1="46" x2="62" y2="62" stroke="#fff" stroke-width="3"/></svg>
  <h2>For Patients</h2>
  <p>Learn how to prepare for your exam, what to expect on the day, where to find our locations and how to reach us with questions.</p>
  <a class="btn-white" href="#">Read More</a>
</section>
<section class="abs audience physicians" role="img" aria-label="Group of smiling doctors and nurses">
  <svg width="80" height="76" viewBox="0 0 80 76"><circle cx="16" cy="10" r="8" fill="#fff"/><rect x="8" y="21" width="16" height="32" rx="3" fill="#fff"/><rect x="10" y="52" width="5" height="22" fill="#fff"/><rect x="17" y="52" width="5" height="22" fill="#fff"/><rect x="30" y="8" width="46" height="38" fill="none" stroke="#fff" stroke-width="4"/><line x1="22" y1="30" x2="40" y2="22" stroke="#fff" stroke-width="4"/><line x1="53" y1="46" x2="44" y2="62" stroke="#fff" stroke-width="3"/><line x1="53" y1="46" x2="62" y2="62" stroke="#fff" stroke-width="3"/></svg>
  <h2>For Physicians</h2>
  <p>Refer patients with ease, request studies online, view images and reports in our secure portal and consult a radiologist directly.</p>
  <a class="btn-white" href="#">Read More</a>
</section>

<div class="abs billpay"><h2 class="block-title">Online Bill Pay</h2></div>
<div class="abs billpay-shot" role="img" aria-label="Hand holding a payment card over a laptop keyboard"></div>
<ul class="abs billpay-links">
  <li><span>➝</span><a href="#">BILLPAY Pine Hollow Imaging</a></li>
  <li><span>➝</span><a href="#">BILLPAY Pine Hollow MRI</a></li>
  <li><span>➝</span><a href="#">BILLPAY Ridgeline Scan Center</a></li>
</ul>

<div class="abs doctors"><h2 class="block-title">Our Physicians</h2></div>
<div class="abs doctor" style="left:628px"><div class="shot" role="img" aria-label="Portrait of physician Mara Linden in a white coat" style="background:linear-gradient(180deg,#f2f4f5,#d9c2ad 40%,#f7f7f7 70%,#e4ecf1)"></div><div class="name">Mara Linden</div></div>
<div class="abs doctor" style="left:734px"><div class="shot" role="img" aria-label="Portrait of physician Ivy Castell in a white coat" style="background:linear-gradient(180deg,#eceff1,#cfb6a2 40%,#f5f5f5 70%,#6d8fb3)"></div><div class="name">Ivy Castell</div></div>
<div class="abs doctor" style="left:840px"><div class="shot" role="img" aria-label="Portrait of physician Owen Harlow in a white coat" style="background:linear-gradient(180deg,#f3f5f6,#c9a88e 40%,#f7f7f7 65%,#3d6fb0)"></div><div class="name">Owen Harlow</div></div>
<div class="abs doctor" style="left:945px"><div class="shot" role="img" aria-label="Portrait of physician Felix Rowe in a white coat" style="background:linear-gradient(180deg,#f5f6f7,#d3b49b 40%,#fafafa 70%,#e9eef2)"></div><div class="name">Felix Rowe</div></div>

<section class="abs reviews"></section>
<h2 class="abs heading reviews-title">Patient Reviews</h2>
<svg class="abs" style="left:0;top:2107px" width="1200" height="30"><line x1="420" y1="15" x2="584" y2="15" stroke="#ccc"/><line x1="616" y1="15" x2="780" y2="15" stroke="#ccc"/><circle cx="600" cy="15" r="9" fill="#8f9fc7"/></svg>
<div class="abs review-avatar" role="img" aria-label="Portrait of the reviewer"></div>
<svg class="abs" style="left:312px;top:2140px" width="34" height="22"><text x="0" y="26" font-family="Georgia,serif" font-size="44" fill="#ccc">“</text></svg>
<p class="abs review-text">&emsp;&emsp;&ensp;From the moment I called to book my MRI, everyone was warm and patient with me. The technologist explained each step, checked that I was comfortable and even found me a blanket. My results reached my doctor the next day, and the notes from the radiologist were clear and thorough. After years of hospital visits, this felt like care from neighbors who truly listen. I would not go anywhere else for imaging in the region.</p>
<div class="abs review-rule"></div>
<p class="abs review-name">- Mr. Toren Vasquel</p>
<svg class="abs" style="left:995px;top:2274px" width="40" height="12"><circle cx="6" cy="6" r="4" fill="none" stroke="#8bbd9a" stroke-width="1.5"/><circle cx="18" cy="6" r="4" fill="#aaa"/><circle cx="30" cy="6" r="4" fill="#aaa"/></svg>

<svg class="abs footer-shape" width="1200" height="278" viewBox="0 0 1200 278">
  <path d="M0 140 Q600 -40 1200 140 L1200 278 L0 278 Z" fill="#333333"/>
  <path d="M0 128 Q600 -48 1200 128" fill="none" stroke="#00b7f1" stroke-width="5"/>
</svg>

<div class="abs footer-col" style="left:207px;width:220px">
  <h3>Quick Links</h3>
  <ul class="links">
    <li>Home</li><li>For Physicians</li><li>About Us</li><li>PACS &amp; Documents</li><li>Our Services</li><li>Appointments</li><li>For Patients</li><li>Our Locations</li><li>Our Physicians</li>
  </ul>
</div>
<div class="abs vrule" style="left:477px"></div>
<div class="abs footer-col inquiry" style="left:522px;width:200px">
  <h3>Quick Inquiry</h3>
  <input placeholder="Name"><input placeholder="Email"><textarea placeholder="Message"></textarea>
  <button>Submit</button>
</div>
<div class="abs vrule" style="left:764px"></div>
<div class="abs footer-col contact" style="left:810px;width:200px">
  <h3>Contact Details</h3>
  <ul>
    <li><svg width="10" height="14" viewBox="0 0 10 14"><path d="M5 0a5 5 0 0 1 5 5c0 4-5 9-5 9S0 9 0 5a5 5 0 0 1 5-5z" fill="#ddd"/><circle cx="5" cy="5" r="2" fill="#333"/></svg><span>2280 NE Juniper Hollow Way<br>Bend, Oregon 97700</span></li>
    <li><svg width="11" height="11" viewBox="0 0 24 24"><path fill="#ddd" d="M6.6 10.8a15 15 0 0 0 6.6 6.6l2.2-2.2c.3-.3.7-.4 1-.2 1.1.4 2.3.6 3.6.6.6 0 1 .4 1 1V20c0 .6-.4 1-1 1A17 17 0 0 1 3 4c0-.6.4-1 1-1h3.5c.6 0 1 .4 1 1 0 1.3.2 2.5.6 3.6.1.3 0 .7-.2 1z"/></svg><span>(555) 014-2290</span></li>
    <li><svg width="12" height="10" viewBox="0 0 12 10"><rect width="12" height="10" fill="#ddd"/><path d="M0 0l6 5 6-5" fill="none" stroke="#333"/></svg><span>info@phipclinic-example.com</span></li>
  </ul>
</div>

<footer class="abs bottom-bar">
  <p>Copyright © 2016 - Pine Hollow Imaging Partners &nbsp;|&nbsp; All Right Reserved.</p>
  <span class="social" style="left:944px;background:var(--green)"></span>
  <span class="social" style="left:977px;background:var(--cyan)"></span>
  <span class="social" style="left:1010px;background:var(--cyan)"></span>
</footer>

</body>
</html>
```